Home Loan Introducer needs logo/business cards

We need a simple but classy logo for business cards and flyers. The business is a home loan referral business that is called an Introducer. The business name is "The Harborline".
I was thinking very simple and straight to the point on the front with "Home Loans" the only thing on the front with a nice background colour/s.
Then on the back, "The Harborline"
and "Quality Customer Service"
and "Email, text or call welcome"
and then my name, email address and phone number.
Updates
Thank you for all the designs :-)
Target Market(s)
Home buyers.
Home owners.
Investors.
Industry/Entity Type
Loan
Look and feel

```html
<!DOCTYPE html>
<html lang="en">
<head>
<meta charset="utf-8">
<title>The Harborline — Business Cards</title>
<link rel="stylesheet" href="https://fonts.googleapis.com/css2?family=Roboto+Mono:wght@700&display=swap">
<style>
  :root {
    --page: #ffffff;
    --card: #0a0a0a;
    --green: #0f7036;
    --leaf: #0b6b33;
    --leaf-soft: rgba(11, 107, 51, 0.6);
    --leaf-clear: rgba(11, 107, 51, 0);
  }
  html, body {
    margin: 0;
    padding: 0;
    width: 1200px;
    height: 750px;
    overflow: hidden;
    background: var(--page);
  }
  .canvas {
    position: relative;
    width: 1200px;
    height: 750px;
  }
  .card {
    position: absolute;
    left: 295px;
    width: 600px;
    height: 308px;
    background: var(--card);
    overflow: hidden;
  }
  .card--front { top: 45px; }
  .card--back { top: 383px; }
  .card-text {
    position: absolute;
    margin: 0;
    color: var(--green);
    font-family: "Roboto Mono", monospace;
    font-weight: 700;
    white-space: nowrap;
    line-height: 1;
  }
  .front-title {
    left: 287px;
    top: 153px;
    font-size: 50px;
    letter-spacing: 2px;
    transform: translate(-50%, -50%) scaleY(1.08);
  }
  .business-name {
    left: 94px;
    top: 155px;
    font-size: 36px;
    letter-spacing: 4.5px;
    transform: translateY(-50%) scaleY(1.05);
  }
  .flourish {
    position: absolute;
    left: 430px;
    top: 100px;
    width: 200px;
    height: 240px;
    background: radial-gradient(ellipse 115px 135px at 135px 155px,
      var(--leaf) 0%, var(--leaf-soft) 45%, var(--leaf-clear) 100%);
  }
</style>
</head>
<body>
  <main class="canvas">
    <section class="card card--front">
      <h1 class="card-text front-title">Home Loans</h1>
    </section>
    <section class="card card--back">
      <p class="card-text business-name">The Harborline</p>
      <div class="flourish" role="img" aria-label="Green leafy vine flourish growing from the bottom-right corner"></div>
    </section>
  </main>
</body>
</html>
```